Dental Practice Billboard Design

We are a newer dental practice in need of a simple but appealing billboard for our growing dental practice to attract new patients. The practice is owned by husband and wife dentists and is family friendly in a small town in Kentucky. We try to be very friendly and caring to our patients. Would prefer a blue background for the billboard and our tooth logo to be prominent. We are partial to the Patua One font used in the image below but please feel free to tweak it as you deem necessary. The shape of the uppercase D and lowercase g are why we like that font, so fonts with a similarly shaped “D” and “g” would work as well. Please include our phone number (555) 847-1390. Please see our website Harlowbrookdentistry.example for more info on the practice if needed. Thank you! Looking forward to seeing your creation.
Updates

The dimensions will be 12ft x 24ft (3.6576m x 7.3152m). Apologies for not including this in the original prompt. Thank you all for your submissions.

Industry/Entity Type

Dental

Font styles to use
Other font styles liked:
• Patua One

Colors
0054AA
0677BA
7BADD7
CADEEF
E8F1F8
0094D4
00A9DD
6FCCEA
C7EBF8
E9F6FB
00AB8E
00BBA5
67D7C9
C6EFE9
E9F9F6
59FF00
82FF00
B8FF75
E3FFCB
F4FFEA

Requirements
Must have
• Phone number, website, Logo, Practice name “Harlow Brook Dentistry”
Should not have
• A tagline or slogan

```html
<!DOCTYPE html>
<html lang="en">
<head>
<meta charset="utf-8">
<title>Harlow Brook Dentistry – Billboard Concepts</title>
<link href="https://fonts.googleapis.com/css2?family=Patua+One&family=Bitter:wght@700&display=swap" rel="stylesheet">
<style>
  :root {
    --sheet-grey: #bdbdbd;
    --stage-grey: #e6e6e8;
    --board-blue: #2a5aa8;
    --brand-green: #22b14c;
    --white: #ffffff;
    --smile-warm: #e8c7bd;
    --smile-pink: #d98a8f;
    --portrait-light: #efe6dc;
    --portrait-dark: #b9a48e;
  }
  * { margin: 0; padding: 0; box-sizing: border-box; }
  html, body { width: 1200px; height: 823px; overflow: hidden; }
  body { background: var(--sheet-grey); position: relative; }

  .stage {
    position: absolute;
    width: 533px; height: 399px;
    background: var(--stage-grey);
    overflow: hidden;
  }
  .stage--left { left: 53px; top: 373px; }
  .stage--right { left: 611px; top: 373px; }

  .billboard {
    position: absolute;
    width: 539px; height: 269px;
    background: var(--board-blue);
    overflow: hidden;
  }
  .billboard--top-left { left: 50px; top: 50px; }
  .billboard--top-right { left: 611px; top: 50px; }
  .stage .billboard {
    left: 47px; top: 90px;
    transform: scale(0.816);
    transform-origin: top left;
  }

  .billboard__photo {
    position: absolute;
    left: 190px; top: 10px;
    width: 160px; height: 184px;
    border-radius: 6px;
  }
  .billboard__photo--dentists {
    background: linear-gradient(160deg, var(--portrait-light) 0%, var(--portrait-dark) 55%, var(--white) 100%);
  }
  .billboard__photo--smile {
    background: linear-gradient(180deg, var(--smile-pink) 0%, var(--white) 40%, var(--smile-warm) 65%, var(--smile-pink) 100%);
  }

  .billboard__phone {
    position: absolute;
    left: 367px; top: 39px;
    height: 32px; padding: 0 12px 0 10px;
    border-radius: 16px;
    background: var(--brand-green);
    color: var(--white);
    font: 17px/32px "Patua One", serif;
    display: flex; align-items: center; gap: 6px;
    white-space: nowrap;
  }
  .billboard__phone svg { width: 15px; height: 15px; }

  .billboard__name {
    position: absolute;
    left: 0; right: 0; top: 199px;
    text-align: center;
    color: var(--white);
    font: 400 35px/1 "Patua One", serif;
    white-space: nowrap;
  }
  .billboard__url {
    position: absolute;
    left: 0; right: 0; top: 240px;
    text-align: center;
    color: var(--white);
    font: 700 14px/1 "Bitter", serif;
    white-space: nowrap;
  }
</style>
</head>
<body>

  <section class="billboard billboard--top-left">
    <div class="billboard__photo billboard__photo--dentists" role="img" aria-label="Logo area with a photo of the two dentists in white coats"></div>
    <div class="billboard__phone">
      <svg viewBox="0 0 24 24" aria-hidden="true"><path fill="#2a5aa8" d="M6.6 10.8a15.5 15.5 0 0 0 6.6 6.6l2.2-2.2a1 1 0 0 1 1-.25 11.4 11.4 0 0 0 3.6.57 1 1 0 0 1 1 1V20a1 1 0 0 1-1 1A17 17 0 0 1 3 4a1 1 0 0 1 1-1h3.5a1 1 0 0 1 1 1c0 1.25.2 2.45.57 3.57a1 1 0 0 1-.25 1z"/></svg>
      (555) 847-1390
    </div>
    <h1 class="billboard__name">Harlow Brook Dentistry</h1>
    <p class="billboard__url">Harlowbrookdentistry.example</p>
  </section>

  <section class="billboard billboard--top-right">
    <div class="billboard__photo billboard__photo--smile" role="img" aria-label="Logo area with a close-up photo of a healthy smile"></div>
    <div class="billboard__phone">
      <svg viewBox="0 0 24 24" aria-hidden="true"><path fill="#2a5aa8" d="M6.6 10.8a15.5 15.5 0 0 0 6.6 6.6l2.2-2.2a1 1 0 0 1 1-.25 11.4 11.4 0 0 0 3.6.57 1 1 0 0 1 1 1V20a1 1 0 0 1-1 1A17 17 0 0 1 3 4a1 1 0 0 1 1-1h3.5a1 1 0 0 1 1 1c0 1.25.2 2.45.57 3.57a1 1 0 0 1-.25 1z"/></svg>
      (555) 847-1390
    </div>
    <h2 class="billboard__name">Harlow Brook Dentistry</h2>
    <p class="billboard__url">Harlowbrookdentistry.example</p>
  </section>

  <div class="stage stage--left">
    <section class="billboard">
      <div class="billboard__photo billboard__photo--dentists" role="img" aria-label="Logo area with a photo of the two dentists in white coats"></div>
      <div class="billboard__phone">
        <svg viewBox="0 0 24 24" aria-hidden="true"><path fill="#2a5aa8" d="M6.6 10.8a15.5 15.5 0 0 0 6.6 6.6l2.2-2.2a1 1 0 0 1 1-.25 11.4 11.4 0 0 0 3.6.57 1 1 0 0 1 1 1V20a1 1 0 0 1-1 1A17 17 0 0 1 3 4a1 1 0 0 1 1-1h3.5a1 1 0 0 1 1 1c0 1.25.2 2.45.57 3.57a1 1 0 0 1-.25 1z"/></svg>
        (555) 847-1390
      </div>
      <h2 class="billboard__name">Harlow Brook Dentistry</h2>
      <p class="billboard__url">Harlowbrookdentistry.example</p>
    </section>
  </div>

  <div class="stage stage--right">
    <section class="billboard">
      <div class="billboard__photo billboard__photo--smile" role="img" aria-label="Logo area with a close-up photo of a healthy smile"></div>
      <div class="billboard__phone">
        <svg viewBox="0 0 24 24" aria-hidden="true"><path fill="#2a5aa8" d="M6.6 10.8a15.5 15.5 0 0 0 6.6 6.6l2.2-2.2a1 1 0 0 1 1-.25 11.4 11.4 0 0 0 3.6.57 1 1 0 0 1 1 1V20a1 1 0 0 1-1 1A17 17 0 0 1 3 4a1 1 0 0 1 1-1h3.5a1 1 0 0 1 1 1c0 1.25.2 2.45.57 3.57a1 1 0 0 1-.25 1z"/></svg>
        (555) 847-1390
      </div>
      <h2 class="billboard__name">Harlow Brook Dentistry</h2>
      <p class="billboard__url">Harlowbrookdentistry.example</p>
    </section>
  </div>

</body>
</html>
```